Residential Remodeling Contractor needs updated business card

I need a new design for my business card.
Name of the company is Ridgefell Construction. I need a card that commands presence, strength, integrity. I have been in business for 28 years. I am a Residential Remodeling Contractor that covers all aspects of a residential remodel and build.

```html
<!DOCTYPE html>
<html lang="en">
<head>
<meta charset="utf-8">
<title>Ridgefell Construction – Business Card</title>
<link rel="stylesheet" href="https://fonts.googleapis.com/css2?family=Montserrat:wght@400;500;600&display=swap">
<style>
  :root {
    --navy: #1f3c82;
    --white: #ffffff;
    --ink: #1b1b1b;
    --backdrop: #e9e9ec;
    --divider: rgba(255,255,255,0.45);
  }
  * { box-sizing: border-box; margin: 0; padding: 0; }
  html, body { width: 1200px; height: 786px; overflow: hidden; }
  body {
    background: var(--backdrop);
    font-family: "Montserrat", sans-serif;
    position: relative;
  }
  .card {
    position: absolute;
    top: 236px;
    width: 550px;
    height: 314px;
    background: var(--navy);
    overflow: hidden;
    box-shadow: 0 6px 18px rgba(0,0,0,0.18);
  }
  .card--contact { left: 36px; }
  .card--brand { left: 614px; }

  .wordmark {
    color: var(--white);
    font-weight: 500;
    text-transform: uppercase;
    letter-spacing: 0.06em;
    line-height: 1.15;
  }

  /* contact side */
  .contact-brand {
    position: absolute;
    left: 40px;
    top: 88px;
    width: 200px;
    display: flex;
    align-items: center;
    gap: 10px;
  }
  .contact-brand .mark-dot {
    width: 14px; height: 14px; border-radius: 50%;
    background: var(--white); flex: none;
  }
  .contact-brand .wordmark { font-size: 17px; }
  .divider {
    position: absolute;
    left: 258px; top: 52px;
    width: 1px; height: 120px;
    background: var(--divider);
  }
  .person { position: absolute; left: 282px; top: 52px; color: var(--white); }
  .person__name { font-size: 20px; font-weight: 600; }
  .person__role { font-size: 11px; font-weight: 400; margin-top: 2px; opacity: 0.85; }
  .contact-list { list-style: none; margin-top: 22px; }
  .contact-list li {
    display: flex; align-items: center; gap: 10px;
    font-size: 11.5px; font-weight: 400; margin-bottom: 9px;
  }
  .contact-list svg { width: 13px; height: 13px; flex: none; }
  .address-band {
    position: absolute;
    left: 0; right: 0; top: 226px; height: 40px;
    background: var(--white);
    display: flex; align-items: center; justify-content: center;
    color: var(--ink); font-size: 13px; font-weight: 500;
  }

  /* brand side */
  .brand-panel {
    position: absolute; inset: 0;
    display: flex; align-items: center; justify-content: flex-end;
    padding-right: 48px;
  }
  .brand-panel .wordmark { font-size: 34px; text-align: left; }
</style>
</head>
<body>

  <section class="card card--contact">
    <div class="contact-brand">
      <span class="mark-dot"></span>
      <span class="wordmark">Ridgefell<br>Construction</span>
    </div>
    <div class="divider"></div>
    <div class="person">
      <p class="person__name">Daniel Hartwell</p>
      <p class="person__role">Owner</p>
      <ul class="contact-list">
        <li>
          <svg viewBox="0 0 16 16" fill="#fff"><path d="M3.6 1.5l2.2 2.7-1.3 1.6c.9 2 2.6 3.7 4.6 4.6l1.6-1.3 2.7 2.2-1.4 2.4C6.6 13.4 2.6 9.4 1.2 2.9z"/></svg>
          555.014.2290
        </li>
        <li>
          <svg viewBox="0 0 16 16" fill="#fff"><rect x="1" y="3" width="14" height="10" rx="1"/><path d="M1.5 3.5 8 9l6.5-5.5" stroke="#1f3c82" stroke-width="1.4" fill="none"/></svg>
          info@ridgefellconstruction.com
        </li>
        <li>
          <svg viewBox="0 0 16 16" fill="none" stroke="#fff" stroke-width="1.4"><circle cx="8" cy="8" r="6.3"/><path d="M1.7 8h12.6M8 1.7c-2.2 2.5-2.2 10.1 0 12.6M8 1.7c2.2 2.5 2.2 10.1 0 12.6"/></svg>
          www.ridgefellconstruction.com
        </li>
      </ul>
    </div>
    <div class="address-band">482 Cedar Hollow Lane Brandon, MS 39047</div>
  </section>

  <section class="card card--brand">
    <div class="brand-panel">
      <span class="wordmark">Ridgefell<br>Construction</span>
    </div>
  </section>

</body>
</html>
```